MRT Property - Business Cards

Looking for a business card & general letterhead, signage etc design for our new logo.

Colours:
000a20
0056a2
00b5ef
0088ce
68cef2

Fonts:
Poppins
Karla

Please keep look and feel of new brand - example in the zip package I sent.

```html
<!DOCTYPE html>
<html lang="en">
<head>
<meta charset="utf-8">
<title>MRT Property – Business Cards</title>
<link rel="stylesheet" href="https://fonts.googleapis.com/css2?family=Poppins:wght@300;400;600&family=Karla:wght@400&display=swap">
<style>
  :root {
    --ink: #000a20;
    --card: #111626;
    --card-edge: #1a2033;
    --deep-blue: #0056a2;
    --brand-blue: #1468c4;
    --sky: #00b5ef;
    --mid-blue: #0088ce;
    --pale-blue: #68cef2;
    --emboss: #4a5164;
    --text-light: #e6e9f0;
    --text-muted: #9aa2b5;
    --stage: #1b1b1d;
  }
  * { box-sizing: border-box; margin: 0; padding: 0; }
  html, body { width: 1200px; height: 852px; overflow: hidden; }
  body {
    background: var(--stage);
    font-family: "Poppins", sans-serif;
    position: relative;
  }
  .card {
    position: absolute;
    top: 283px;
    width: 500px;
    height: 286px;
    border-radius: 22px;
    background: linear-gradient(160deg, var(--card-edge), var(--card));
    overflow: hidden;
  }
  .card--back { left: 70px; }
  .card--front { left: 630px; }

  /* back side */
  .back-wordmark {
    position: absolute;
    left: 40px; top: 90px;
    font-weight: 600;
    font-size: 50px;
    line-height: 1;
    color: var(--emboss);
    white-space: nowrap;
  }
  .back-web {
    position: absolute;
    right: 34px; bottom: 30px;
    font-family: "Karla", sans-serif;
    font-size: 11px;
    letter-spacing: 5px;
    color: var(--text-muted);
  }
  .back-band {
    position: absolute;
    left: 0; right: 0; bottom: 0;
    height: 9px;
    background: var(--deep-blue);
  }

  /* front side */
  .front-mark {
    position: absolute;
    left: 32px; top: 128px;
    font-weight: 600;
    font-size: 46px;
    line-height: 1.05;
    color: var(--mid-blue);
  }
  .front-wordmark {
    position: absolute;
    right: 30px; top: 26px;
    font-weight: 600;
    font-size: 26px;
    line-height: 1.2;
    color: var(--brand-blue);
  }
  .holder {
    position: absolute;
    right: 30px; top: 82px;
    text-align: right;
  }
  .holder-name {
    font-weight: 600;
    font-size: 18px;
    color: var(--mid-blue);
    line-height: 1.2;
  }
  .holder-title {
    font-size: 10px;
    font-weight: 300;
    color: var(--text-light);
  }
  .contact {
    position: absolute;
    right: 30px; top: 150px;
    list-style: none;
    text-align: right;
    font-family: "Karla", sans-serif;
    font-size: 12.5px;
    color: var(--text-light);
    line-height: 21px;
  }
  .contact-item { display: flex; justify-content: flex-end; align-items: center; gap: 8px; white-space: nowrap; }
  .contact-icon { width: 13px; height: 13px; display: block; }
  .contact-spacer { width: 13px; }
</style>
</head>
<body>
  <section class="card card--back" aria-label="Business card back">
    <div class="back-wordmark">MRT Property</div>
    <div class="back-web">www.mrtproperty.com</div>
    <div class="back-band"></div>
  </section>

  <section class="card card--front" aria-label="Business card front">
    <div class="front-mark">MRT<br>Property</div>
    <div class="front-wordmark">MRT Property</div>
    <div class="holder">
      <p class="holder-name">Daniel Hart</p>
      <p class="holder-title">Managing Director</p>
    </div>
    <ul class="contact">
      <li class="contact-item">555-010-2020
        <svg class="contact-icon" viewBox="0 0 16 16" aria-hidden="true"><path fill="#0088ce" d="M3.5 1.5l2.5 0 1 3.5-1.6 1.2a8 8 0 0 0 4.4 4.4L11 9l3.5 1v2.5c0 1-1 2-2 2A11 11 0 0 1 1.5 3.5c0-1 1-2 2-2z"/></svg>
      </li>
      <li class="contact-item">daniel@mrtproperty.com
        <svg class="contact-icon" viewBox="0 0 16 16" aria-hidden="true"><rect x="1" y="3" width="14" height="10" rx="1.5" fill="#0088ce"/><path d="M1.5 4l6.5 5 6.5-5" fill="none" stroke="#111626" stroke-width="1.3"/></svg>
      </li>
      <li class="contact-item">www.mrtproperty.com
        <svg class="contact-icon" viewBox="0 0 16 16" aria-hidden="true"><circle cx="8" cy="8" r="6.5" fill="#0088ce"/><g fill="none" stroke="#111626" stroke-width="1"><ellipse cx="8" cy="8" rx="2.8" ry="6.5"/><path d="M1.5 8h13M2.5 5h11M2.5 11h11"/></g></svg>
      </li>
      <li class="contact-item">27 Harbour View Road Northgate<span class="contact-spacer"></span></li>
    </ul>
  </section>
</body>
</html>
```